Business Card design for law firm = Brightvale Australia

We are seeking a new design for our business cards.
We are keeping our logo, which is attached.
We need space for
Name
Title
Address is , which is
Level 7
214 Marlowe Street
Sydney NSW 2047
Phone :
Mobile :
Fax :
Email :
DX :
website www.brightvale-example.com.au

Industry/Entity Type

Law Firm / Banking and Finance

Contact Information for Business Card

We are seeking a new design for our business cards. We are keeping our logo. We need space for Name Title Address is Level 7 214 Marlowe Street Sydney NSW 2047 Phone Mobile Fax Email DX website www.brightvale-example.com.au

Colors
0054AA
0677BA
7BADD7
CADEEF
E8F1F8

Requirements
Must have
• see our website for general feel www.brightvale-example.com.au

```html
<!DOCTYPE html>
<html lang="en">
<head>
<meta charset="utf-8">
<title>Brightvale Australia – Business Card</title>
<link rel="stylesheet" href="https://fonts.googleapis.com/css2?family=Nunito+Sans:wght@400;600;700&display=swap">
<style>
  :root {
    --backdrop: #aaaaaa;
    --card-white: #ffffff;
    --navy: #042f5b;
    --brand-blue: #0054aa;
    --brand-teal: #0799c4;
    --link-teal: #0a93c2;
    --text-light: #ffffff;
  }
  html, body {
    margin: 0;
    padding: 0;
    width: 1200px;
    height: 1000px;
    overflow: hidden;
    background: var(--backdrop);
    font-family: "Nunito Sans", "Avenir Next", Arial, sans-serif;
  }
  .canvas {
    position: relative;
    width: 1200px;
    height: 1000px;
  }
  .card {
    position: absolute;
    left: 343px;
    width: 514px;
    height: 296px;
  }
  .card--front { top: 146px; background: var(--card-white); }
  .card--back  { top: 489px; background: var(--navy); color: var(--text-light); }

  .brand {
    position: absolute;
    margin: 0;
    font-weight: 400;
    line-height: 1;
    white-space: nowrap;
  }
  .card--front .brand {
    left: 60px;
    top: 164px;
    font-size: 44px;
    color: var(--brand-blue);
    letter-spacing: -0.5px;
  }
  .card--back .brand {
    left: 336px;
    top: 218px;
    font-size: 23px;
    color: var(--text-light);
  }

  .contact { position: absolute; left: 61px; top: 44px; }
  .contact__name { margin: 0; font-size: 17px; font-weight: 700; line-height: 20px; letter-spacing: 0.2px; }
  .contact__title { margin: 0; font-size: 14px; font-weight: 400; line-height: 18px; }
  .contact__rule { width: 79px; height: 3px; background: var(--brand-teal); margin: 7px 0 15px; border: 0; }
  .contact__block { margin: 0 0 13px; font-size: 12px; line-height: 14.5px; font-style: normal; }
  .contact__web { margin: 15px 0 0; font-size: 12px; font-weight: 700; color: var(--link-teal); }
</style>
</head>
<body>
<main class="canvas">
  <section class="card card--front" aria-label="Card front">
    <p class="brand">Brightvale</p>
  </section>

  <section class="card card--back" aria-label="Card back">
    <div class="contact">
      <h1 class="contact__name">Helena Marsh</h1>
      <p class="contact__title">Chief Legal Officer</p>
      <hr class="contact__rule">
      <address class="contact__block">
        Level 7<br>
        214 Marlowe Street<br>
        Sydney NSW 2047
      </address>
      <p class="contact__block">
        P: 02 9000 0122<br>
        M:<br>
        F: 02 9000 6411<br>
        E: enquiries@brightvale-example.com.au<br>
        DX: 912 Sydney
      </p>
      <p class="contact__web">www.brightvale-example.com.au</p>
    </div>
    <p class="brand">Brightvale</p>
  </section>
</main>
</body>
</html>
```